ULMIRA card Technical Architecture

Hello everyone ULMIRA: It is a consulting firm in Architecture and Construction. I require a card duplexing, sober, elegant, classic but not boring. Update 1: Use the following data for the card. Name: Gonzalo Pereda Mauricio Villalta Position: COO Twitter: @ulmiraAT Homepage: ulmira-example.com home address not include the participation of all thank you.

Target Market(s)

Construction companies, Architects and Consulting Engineers

Industry/Entity Type

Consulting

Contact Information for Business Card

Los campos que debe tener:
Nombre, Cargo, email, homepage y twitter

Font styles to use
Serif
Sans Serif
Other font styles liked:
• Me gustan playfair display, open sans y roboto, pero estoy sujeto a sus propuestas

Requirements
Must have
• Colors: Present combined proposals in white, red, gray and black Update 1: The two names must be clearly differentiated from the two surnames
Nice to have
• They are free to present their best proposals. I will bring them immediate feedback to the extent you can go see their designs. Complete data for card and logo files will give the winner the

```html
<!DOCTYPE html>
<html lang="es">
<head>
<meta charset="utf-8">
<title>ULMIRA – Business Card</title>
<link rel="stylesheet" href="https://fonts.googleapis.com/css2?family=Source+Sans+3:wght@400;600&display=swap">
<style>
  :root {
    --backdrop-top: #999999;
    --backdrop-bottom: #7a7a7a;
    --card-light: #f3f3f3;
    --brand-red: #880000;
    --accent-red: #d0142c;
    --ink: #111111;
    --white: #ffffff;
  }
  html, body {
    margin: 0;
    padding: 0;
    width: 1200px;
    height: 900px;
    overflow: hidden;
  }
  body {
    position: relative;
    background: linear-gradient(to bottom, var(--backdrop-top), var(--backdrop-bottom));
    font-family: "Source Sans 3", sans-serif;
  }
  .card {
    position: absolute;
    top: 184px;
    width: 301px;
    height: 490px;
    border-radius: 12px;
    box-sizing: border-box;
  }
  .card--front {
    left: 299px;
    background: var(--card-light);
    text-align: center;
    color: var(--ink);
  }
  .card--back {
    left: 645px;
    width: 305px;
    background: var(--brand-red);
    display: flex;
    align-items: center;
    justify-content: center;
  }
  .brand {
    position: absolute;
    top: 96px;
    left: 0;
    right: 0;
    display: flex;
    flex-direction: column;
    align-items: center;
  }
  .brand__square {
    width: 14px;
    height: 14px;
    background: var(--accent-red);
    margin-bottom: 14px;
  }
  .brand__name {
    font-size: 30px;
    font-weight: 400;
    letter-spacing: 7px;
    line-height: 1;
    color: var(--ink);
    margin: 0;
    padding-left: 7px;
  }
  .person {
    position: absolute;
    top: 272px;
    left: 0;
    right: 0;
  }
  .person__name {
    margin: 0;
    font-size: 16px;
    font-weight: 600;
    color: var(--accent-red);
    line-height: 20px;
  }
  .person__role {
    margin: 0;
    font-size: 14px;
    line-height: 18px;
  }
  .contact {
    position: absolute;
    top: 330px;
    left: 0;
    right: 0;
    margin: 0;
    padding: 0;
    list-style: none;
    font-size: 14px;
    line-height: 18px;
  }
  .back-name {
    font-size: 40px;
    font-weight: 400;
    letter-spacing: 9px;
    padding-left: 9px;
    color: var(--white);
    margin: 0 0 10px;
  }
</style>
</head>
<body>
  <section class="card card--front">
    <div class="brand">
      <span class="brand__square"></span>
      <p class="brand__name">ULMIRA</p>
    </div>
    <div class="person">
      <p class="person__name">Daniel Herrera</p>
      <p class="person__role">Managing Director</p>
    </div>
    <ul class="contact">
      <li>555 014 272</li>
      <li>info@ulmira-example.com</li>
      <li>www.ulmira-example.com</li>
      <li>@ulmiraAT</li>
    </ul>
  </section>

  <section class="card card--back">
    <p class="back-name">ULMIRA</p>
  </section>
</body>
</html>
```